Corporate Business Card

Very professional, Modern, Not to busy, include phone address email, website
(253) 617-4930, 18761 52nd Avenue S, Kent, WA 98047, martin@plumlinegroup.com, varkoworks.com

Target Market(s)

Manufacturing

Industry/Entity Type

Aero, machining, manufacturing, Off road racing

Contact Information for Business Card

Phone, address email, website

```html
<!DOCTYPE html>
<html lang="en">
<head>
<meta charset="utf-8">
<title>Varko Works – Business Card</title>
<link href="https://fonts.googleapis.com/css2?family=Orbitron:wght@700&family=Roboto:wght@400;700&display=swap" rel="stylesheet">
<style>
  :root {
    --navy: #22356b;
    --red: #c42026;
    --card: #ededed;
    --stage: #2c2c2c;
    --rule: #9a9a9a;
  }
  html, body {
    margin: 0;
    padding: 0;
    width: 1200px;
    height: 1138px;
    overflow: hidden;
    background: var(--stage);
  }
  .card {
    position: absolute;
    background: var(--card);
    border-radius: 16px;
    overflow: hidden;
    font-family: "Roboto", Arial, sans-serif;
  }
  .card--front { left: 274px; top: 186px; width: 623px; height: 376px; }
  .card--back  { left: 276px; top: 608px; width: 618px; height: 374px; }

  .brand-name {
    position: absolute;
    margin: 0;
    color: var(--navy);
    font-family: "Roboto", Arial, sans-serif;
    font-weight: 700;
    text-transform: uppercase;
    white-space: nowrap;
  }
  .card--front .brand-name {
    left: 0; right: 0; top: 140px;
    text-align: center;
    font-size: 58px;
    letter-spacing: 2px;
    line-height: 1;
  }
  .card--back .brand-name {
    left: 34px; width: 236px; top: 166px;
    text-align: center;
    font-size: 32px;
    letter-spacing: 1px;
    line-height: 1;
  }

  .front-web {
    position: absolute;
    left: 0; right: 0; top: 326px;
    text-align: center;
    font-size: 16px;
    color: #222;
    line-height: 20px;
  }
  .front-web__rule {
    position: absolute;
    top: 335px;
    width: 72px;
    height: 3px;
    background: var(--red);
    clip-path: polygon(0 50%, 100% 0, 100% 100%);
  }
  .front-web__rule--left { left: 130px; }
  .front-web__rule--right { left: 422px; transform: scaleX(-1); }

  .color-band {
    position: absolute;
    left: 0; right: 0; bottom: 0;
    height: 10px;
    display: flex;
  }
  .color-band span { flex: 1; }
  .color-band .navy { background: var(--navy); }
  .color-band .red { background: var(--red); }

  .divider {
    position: absolute;
    left: 302px; top: 92px;
    width: 1px; height: 192px;
    background: var(--rule);
  }
  .person-name {
    position: absolute;
    left: 330px; top: 106px;
    margin: 0;
    font-family: "Orbitron", "Roboto", sans-serif;
    font-weight: 700;
    font-size: 22px;
    color: var(--navy);
    letter-spacing: 0.5px;
  }
  .contact-list {
    position: absolute;
    left: 336px; top: 146px;
    margin: 0; padding: 0;
    list-style: none;
    color: var(--navy);
    font-size: 16px;
    line-height: 24px;
  }
  .contact-list li {
    display: flex;
    align-items: flex-start;
  }
  .contact-list .icon {
    width: 14px; height: 14px;
    margin: 5px 12px 0 0;
    flex: none;
    fill: var(--red);
  }
  .contact-list .icon--none { visibility: hidden; }
</style>
</head>
<body>

<section class="card card--front">
  <h1 class="brand-name">Varko Works</h1>
  <span class="front-web__rule front-web__rule--left"></span>
  <div class="front-web">www.varkoworks.com</div>
  <span class="front-web__rule front-web__rule--right"></span>
  <div class="color-band"><span class="navy"></span><span class="red"></span></div>
</section>

<section class="card card--back">
  <p class="brand-name">Varko Works</p>
  <div class="divider"></div>
  <h2 class="person-name">MARTIN HALE</h2>
  <ul class="contact-list">
    <li>
      <svg class="icon" viewBox="0 0 16 16" aria-hidden="true"><path d="M1 5c0-2 3-3 7-3s7 1 7 3v1h-3.5V4.5h-7V6H1zM4 7h8l2 6H2z"/></svg>
      (253) 617-4930
    </li>
    <li>
      <svg class="icon" viewBox="0 0 16 16" aria-hidden="true"><path d="M1 3h14v10H1zM2.5 4.5 8 9l5.5-4.5v1.3L8 10.5 2.5 5.8z" fill-rule="evenodd"/></svg>
      martin@plumlinegroup.com
    </li>
    <li>
      <svg class="icon" viewBox="0 0 16 16" aria-hidden="true"><path d="M8 0a5.5 5.5 0 0 0-5.5 5.5C2.5 10 8 16 8 16s5.5-6 5.5-10.5A5.5 5.5 0 0 0 8 0zm0 3.3a2.2 2.2 0 1 1 0 4.4 2.2 2.2 0 0 1 0-4.4z" fill-rule="evenodd"/></svg>
      18761 52nd Avenue S,
    </li>
    <li>
      <svg class="icon icon--none" viewBox="0 0 16 16" aria-hidden="true"></svg>
      Kent, WA 98047
    </li>
    <li>
      <svg class="icon" viewBox="0 0 16 16" aria-hidden="true"><path d="M8 1a7 7 0 1 0 0 14A7 7 0 0 0 8 1zm-1 1.6C6 4 5.5 5.6 5.4 7H2.6A5.5 5.5 0 0 1 7 2.6zm2 0A5.5 5.5 0 0 1 13.4 7h-2.8C10.5 5.6 10 4 9 2.6zM8 3c.8 1.2 1.3 2.6 1.4 4H6.6C6.7 5.6 7.2 4.2 8 3zM2.6 9h2.8c.1 1.4.6 3 1.6 4.4A5.5 5.5 0 0 1 2.6 9zm4 0h2.8c-.1 1.4-.6 2.8-1.4 4-.8-1.2-1.3-2.6-1.4-4zm4 0h2.8A5.5 5.5 0 0 1 9 13.4c1-1.4 1.5-3 1.6-4.4z" fill-rule="evenodd"/></svg>
      www.varkoworks.com
    </li>
  </ul>
</section>

</body>
</html>
```